Clean business card with logo provided

I want a card that will stand out among the masses. I need the color and image to show professionalism and yet have a family appeal showing that I only deal with win/win scenarios. The back of the card will be used to take notes about the individual so I can use that in my database entry. I like modern design but need professionalism in it also. It needs to fit my "clean, safe, and affordable housing" motto. I need to be able to write on the file and update the card details for my employees.

Target Market(s)

Investors looking to make investment income through real estate

Industry/Entity Type

Real Estate

Contact Information for Business Card

Brent Kovalich
blank address, city, st, zip code
480-555-3174
brentkovalich@ridgeworthrentals.example
www.ridgeworthrentals.example

Font styles to use
Sans Serif

Requirements
Must have
• I would like the back of the card to have lines for info. example
• Met/Visited: Date:
• Interets:
Nice to have
• I want the cards color to match the logo background color. Font with details to be san serif and black. I want the card rectangular with square corners. Standard business card size. I would like to see cards designed with both images to see which i prefer more.

```html
<!DOCTYPE html>
<html lang="en">
<head>
<meta charset="utf-8">
<title>Ridgeworth Rentals LLC – Business Card</title>
<link rel="stylesheet" href="https://fonts.googleapis.com/css2?family=Open+Sans:wght@400;600;700&display=swap">
<style>
  :root {
    --backdrop: #3b3532;
    --card: #f7f7f7;
    --teal: #00b3cc;
    --ink: #1c1c1c;
    --rule: #222222;
    --white: #ffffff;
  }
  * { box-sizing: border-box; margin: 0; padding: 0; }
  html, body {
    width: 1200px; height: 844px; overflow: hidden;
    background: var(--backdrop);
    font-family: "Open Sans", Arial, sans-serif;
  }
  .stage { position: relative; width: 1200px; height: 844px; }

  .card {
    position: absolute; top: 272px;
    width: 525px; height: 300px;
    background: var(--card);
    overflow: hidden;
    box-shadow: 0 14px 30px rgba(0,0,0,.45);
  }
  .card--front { left: 50px; }
  .card--back  { left: 625px; }

  /* Front */
  .front-band {
    position: absolute; left: 0; right: 0; bottom: 0; height: 44px;
    background: var(--teal);
  }
  .front-band::before {
    content: ""; position: absolute; left: 0; right: 0; top: 10px; height: 4px;
    background: var(--white);
  }
  .front-corner {
    position: absolute; right: 14px; bottom: 52px;
    width: 16px; height: 16px; border-radius: 50%;
    background: var(--teal);
  }

  .brand {
    position: absolute; right: 34px; top: 26px; text-align: right;
  }
  .brand__row { display: flex; align-items: center; justify-content: flex-end; gap: 10px; }
  .brand__mark {
    width: 22px; height: 22px; border-radius: 50%; background: var(--teal);
  }
  .brand__name {
    color: var(--teal); font-weight: 600; font-size: 27px; letter-spacing: .5px;
    line-height: 1.1;
  }
  .brand__tagline {
    margin-top: 4px; color: var(--teal); font-size: 10.5px; font-weight: 400;
  }

  .contact { position: absolute; left: 34px; top: 104px; color: var(--ink); }
  .contact__name { color: var(--teal); font-weight: 700; font-size: 18px; line-height: 1.3; margin-bottom: 8px; }
  .contact__address { font-size: 13.5px; line-height: 1.3; margin-bottom: 8px; }
  .contact__list { list-style: none; font-size: 13.5px; line-height: 20px; }
  .contact__list li { display: flex; align-items: center; gap: 10px; }
  .contact__icon { width: 12px; height: 12px; flex: none; }

  /* Back */
  .back-band {
    position: absolute; left: 0; right: 0; top: 0; height: 46px;
    background: var(--teal);
  }
  .back-band::after {
    content: ""; position: absolute; left: 0; right: 0; bottom: 8px; height: 4px;
    background: var(--white);
  }
  .back-corner {
    position: absolute; right: 14px; top: 10px;
    width: 16px; height: 16px; border-radius: 50%;
    background: var(--white);
  }

  .notes { position: absolute; left: 0; top: 80px; width: 100%; }
  .note { position: absolute; height: 40px; }
  .note__label {
    position: absolute; right: 0; top: 0;
    color: var(--teal); font-weight: 700; font-size: 13px; letter-spacing: .3px;
  }
  .note__line {
    position: absolute; left: 0; right: 0; bottom: 0; height: 1.5px; background: var(--rule);
  }
  .note__line::after {
    content: ""; position: absolute; right: -4px; top: -4px;
    width: 9px; height: 9px; border-radius: 50%; background: var(--rule);
  }
  .note--visited  { left: 40px;  width: 300px; top: 0; }
  .note--interests{ left: 100px; width: 300px; top: 70px; }
  .note--problems { left: 160px; width: 300px; top: 140px; }
</style>
</head>
<body>
<main class="stage">

  <section class="card card--front" aria-label="Card front">
    <div class="brand">
      <div class="brand__row">
        <span class="brand__mark" aria-hidden="true"></span>
        <span class="brand__name">Ridgeworth Rentals LLC</span>
      </div>
      <p class="brand__tagline">Providing clean, safe, and affordable housing</p>
    </div>

    <div class="contact">
      <h1 class="contact__name">Brent Kovalich</h1>
      <p class="contact__address">12345, Address Goes Here<br>Country Name, 123456</p>
      <ul class="contact__list">
        <li>
          <svg class="contact__icon" viewBox="0 0 16 16" aria-hidden="true"><path fill="#00b3cc" d="M3.6 1.5l2.3 2.6-1.2 1.8c.9 2 2.5 3.6 4.5 4.5l1.8-1.2 2.6 2.3-1.4 2.3C7 13.3 2.7 9 1.3 2.9z"/></svg>
          <span>480-555-3174</span>
        </li>
        <li>
          <svg class="contact__icon" viewBox="0 0 16 16" aria-hidden="true"><rect x="1" y="3" width="14" height="10" fill="#00b3cc"/><path d="M1.5 3.5L8 9l6.5-5.5" stroke="#fff" stroke-width="1.3" fill="none"/></svg>
          <span>brentkovalich@ridgeworthrentals.example</span>
        </li>
        <li>
          <svg class="contact__icon" viewBox="0 0 16 16" aria-hidden="true"><circle cx="8" cy="8" r="7" fill="#00b3cc"/><path d="M1 8h14M8 1c-3 3-3 11 0 14M8 1c3 3 3 11 0 14" stroke="#fff" stroke-width="1" fill="none"/></svg>
          <span>www.ridgeworthrentals.example</span>
        </li>
      </ul>
    </div>

    <span class="front-corner" aria-hidden="true"></span>
    <div class="front-band" aria-hidden="true"></div>
  </section>

  <section class="card card--back" aria-label="Card back">
    <div class="back-band" aria-hidden="true"></div>
    <span class="back-corner" aria-hidden="true"></span>

    <div class="notes">
      <div class="note note--visited">
        <span class="note__label">VISITED DATE:</span>
        <span class="note__line" aria-hidden="true"></span>
      </div>
      <div class="note note--interests">
        <span class="note__label">INTERETS:</span>
        <span class="note__line" aria-hidden="true"></span>
      </div>
      <div class="note note--problems">
        <span class="note__label">PROBLEMS:</span>
        <span class="note__line" aria-hidden="true"></span>
      </div>
    </div>
  </section>

</main>
</body>
</html>
```